Brellwick Partners, LLC Stationary

Brellwick Partners, LLC is a new financial planning and consulting company. We are looking for designs on business cards, letterhead, envelopes, and anything else that would be useful. Our preference for business card design is two sided. We are looking for a professional and clean look with incorporating the logo and patriotic feel. Thank you to all who participate and good luck!

```html
<!DOCTYPE html>
<html lang="en">
<head>
<meta charset="utf-8">
<title>Brellwick Partners, LLC Stationery</title>
<link rel="stylesheet" href="https://fonts.googleapis.com/css2?family=Exo+2:wght@400;600&display=swap">
<style>
  :root {
    --backdrop: #e8e8e8;
    --paper: #f3f3f3;
    --navy: #224870;
    --navy-deep: #0d3660;
    --red: #b8313a;
    --ink: #4a4f57;
    --white: #ffffff;
  }
  * { box-sizing: border-box; margin: 0; padding: 0; }
  html, body { width: 1200px; height: 821px; overflow: hidden; background: var(--backdrop); }
  body { position: relative; font-family: "Exo 2", sans-serif; color: var(--ink); }

  .sheet {
    position: absolute;
    background: var(--paper);
    box-shadow: 0 2px 6px rgba(0,0,0,0.12);
    overflow: hidden;
  }
  .sheet svg.wave { position: absolute; left: 0; top: 0; width: 100%; height: 100%; }

  .brand { position: absolute; display: flex; align-items: center; gap: 6px; }
  .brand-dot { width: 14px; height: 14px; border-radius: 50%; background: var(--red); flex: none; }
  .brand-block { display: flex; flex-direction: column; }
  .brand-name { font-weight: 600; font-size: 15px; letter-spacing: 0.02em; color: var(--navy); line-height: 1; }
  .brand-tag { font-weight: 600; font-size: 4px; letter-spacing: 0.12em; color: var(--navy); text-transform: uppercase; margin-top: 3px; }

  /* Letterhead */
  .letterhead { left: 70px; top: 110px; width: 466px; height: 662px; }
  .letterhead .brand { left: 26px; top: 58px; }
  .contact-list { position: absolute; right: 20px; top: 593px; list-style: none; text-align: right; }
  .contact-list li { display: flex; justify-content: flex-end; align-items: center; gap: 4px; font-size: 7.5px; color: var(--white); height: 11.5px; }
  .contact-list svg { width: 7px; height: 7px; fill: var(--white); }
  .letterhead .address { position: absolute; right: 17px; top: 643px; font-size: 7.5px; color: var(--white); }

  /* Envelope front */
  .envelope-front { left: 613px; top: 224px; width: 523px; height: 249px; }
  .envelope-front .brand { left: 22px; top: 36px; }
  .return-address { position: absolute; left: 22px; top: 65px; font-size: 7.5px; line-height: 10px; color: var(--ink); }

  /* Envelope back */
  .envelope-back { left: 619px; top: 512px; width: 523px; height: 250px; }
  .flap {
    position: absolute; left: 11px; top: 3px; width: 501px; height: 86px;
    background: var(--navy-deep);
    border-radius: 0 0 10px 10px;
    display: flex; align-items: center; justify-content: center; gap: 6px;
  }
  .flap .brand-dot { background: var(--white); }
  .flap .brand-name { color: var(--white); font-size: 12px; }
</style>
</head>
<body>

  <section class="sheet letterhead" aria-label="Letterhead">
    <svg class="wave" viewBox="0 0 466 662" preserveAspectRatio="none" aria-hidden="true">
      <path d="M0 634 C60 648 130 654 200 636 C290 612 370 585 466 581 L466 662 L0 662 Z" fill="var(--navy)"/>
      <path d="M0 627 C60 641 130 647 200 629 C290 605 370 578 466 574 L466 577 C370 581 290 608 200 633 C130 651 60 645 0 632 Z" fill="var(--red)"/>
    </svg>
    <div class="brand">
      <span class="brand-dot"></span>
      <div class="brand-block">
        <span class="brand-name">BRELLWICK PARTNERS, LLC</span>
        <span class="brand-tag">Financial planning and consulting</span>
      </div>
    </div>
    <ul class="contact-list">
      <li>555 214 7730
        <svg viewBox="0 0 10 10"><path d="M2 0.5 L4 2.5 L3 4 C3.8 5.6 4.6 6.4 6 7 L7.5 6 L9.5 8 L8 9.5 C4 9 1 6 0.5 2 Z"/></svg></li>
      <li>555 214 7731
        <svg viewBox="0 0 10 10"><path d="M2.5 0.5 H7.5 V3 H2.5 Z M0.5 3.5 H9.5 V7.5 H8 V6 H2 V7.5 H0.5 Z M2.5 6.5 H7.5 V9.5 H2.5 Z"/></svg></li>
      <li>hello@brellwick.com
        <svg viewBox="0 0 10 10"><path d="M0.5 2 H9.5 V8 H0.5 Z M1 2.5 L5 5.5 L9 2.5" fill="var(--white)" stroke="var(--navy)" stroke-width="0.8"/></svg></li>
      <li>www.brellwick.com
        <svg viewBox="0 0 10 10"><circle cx="5" cy="5" r="4.5"/><path d="M5 0.5 V9.5 M0.5 5 H9.5 M5 0.5 C2.5 3 2.5 7 5 9.5 M5 0.5 C7.5 3 7.5 7 5 9.5" stroke="var(--navy)" stroke-width="0.6" fill="none"/></svg></li>
    </ul>
    <p class="address">412 Larkspur Road, Fairbanks, Alaska 99701</p>
  </section>

  <section class="sheet envelope-front" aria-label="Envelope front">
    <svg class="wave" viewBox="0 0 523 249" preserveAspectRatio="none" aria-hidden="true">
      <path d="M0 227 C50 240 100 246 160 238 C260 222 380 165 470 166 C495 166 510 167 523 170 L523 249 L0 249 Z" fill="var(--navy)"/>
      <path d="M0 219 C50 232 100 238 160 230 C260 214 380 159 470 160 C495 160 510 161 523 163 L523 165 C510 163 495 163 470 163 C380 162 260 218 160 235 C100 243 50 237 0 224 Z" fill="var(--red)"/>
    </svg>
    <div class="brand">
      <span class="brand-dot"></span>
      <div class="brand-block">
        <span class="brand-name">BRELLWICK PARTNERS, LLC</span>
        <span class="brand-tag">Financial planning and consulting</span>
      </div>
    </div>
    <p class="return-address">412 Larkspur Road<br>Fairbanks, Alaska 99701</p>
  </section>

  <section class="sheet envelope-back" aria-label="Envelope back">
    <div class="flap">
      <span class="brand-dot"></span>
      <span class="brand-name">BRELLWICK PARTNERS, LLC</span>
    </div>
  </section>

</body>
</html>
```